Tessel - Web Design Project

We are seeking to have our website redesigned. Our current webpage is rather dated looking www.tessel-momentum.example We will be utilizing similar content to explain our services as what is in the website now. We do not see it at a retail portal but rather a website for those inquiring about our services as a reference check so to speak.

We wish to have a look that is considered clean, fresh, contemporary and contains a business savvy vibe.

We prefer isolated white background and also wish to retain the integrity of our Logo and colour scheme.

We are looking for something that doesnt look like it was designed at home on sitenook. We are hoping to find something that looks like it would reside on a tablet.

Hello designers!

We apologize for our tardiness as we have been quite preoccupied. We will be extending our invites to the end of January!

Hello All,

Please review our offer once again for updated requirements.  We are hoping to accept a design by months end.

Tessel

Target Market(s)

Business to business clients and Large manufacturers

Industry/Entity Type

Retail

Requirements
Must have
• Existing Logo

There must be an area dedicated to an intro video that will be incorporated on our landing page.

We require design of the other pages as well not only the landing page.

```html
<!DOCTYPE html>
<html lang="en">
<head>
<meta charset="utf-8">
<title>Tessel Performance Group</title>
<link href="https://fonts.googleapis.com/css2?family=Source+Sans+3:ital,wght@0,400;0,600;1,400&family=Bebas+Neue&display=swap" rel="stylesheet">
<style>
:root{
  --red:#e3000f;
  --red-dark:#c4000c;
  --ink:#555;
  --ink-dark:#333;
  --grey-bar:#4a4546;
  --rule:#b9b9b9;
  --white:#fff;
}
*{box-sizing:border-box;margin:0;padding:0}
html,body{width:1108px;height:1200px;overflow:hidden;background:var(--white)}
body{position:relative;font-family:"Source Sans 3",Arial,sans-serif;color:var(--ink)}
.top-bar{position:absolute;left:0;top:0;width:1108px;height:3px;background:var(--grey-bar)}
.util-tab{position:absolute;top:0;height:24px;background:var(--grey-bar);border-radius:0 0 6px 6px;color:var(--white);font-size:13px;display:flex;align-items:center}
.util-tab.search{left:832px;width:32px;justify-content:center}
.util-tab.account{left:878px;width:118px;padding-left:10px;gap:6px}
.util-tab .muted{color:#aaa}
.logo{position:absolute;left:124px;top:34px;display:flex;align-items:center;gap:8px}
.logo-mark{width:14px;height:14px;border-radius:50%;background:var(--red)}
.logo-name{font-size:44px;font-weight:400;color:#666;letter-spacing:-1px;line-height:1}
.main-nav{position:absolute;top:65px;right:111px;display:flex;gap:21px;font-size:13px;text-transform:uppercase;color:#666}
.main-nav a{color:inherit;text-decoration:none;padding:5px 0}
.main-nav a.active{background:#eee;padding:5px 7px;box-shadow:-3px 2px 3px #bbb;color:#555}
.dashed{position:absolute;height:0;border-top:2px dashed var(--rule)}
.hero{position:absolute;left:111px;top:159px;width:886px;height:422px;box-shadow:0 8px 10px -8px #999}
.hero > *{position:absolute}
.video{left:0;top:0;width:454px;height:256px;background:#2e2e2e}
.video-still{position:absolute;left:0;top:0;width:454px;height:228px;background:radial-gradient(circle at 70% 40%,#6e6e6e,#3a3a3a 70%)}
.play{position:absolute;left:198px;top:94px;width:56px;height:56px}
.play-label{position:absolute;left:0;width:454px;top:157px;text-align:center;font-size:11px;color:#bbb}
.controls{position:absolute;left:0;top:228px;width:454px;height:28px;background:#111;display:flex;align-items:center}
.controls .btn{width:24px;height:28px;background:#2a2a2a;display:flex;align-items:center;justify-content:center}
.track{flex:1;margin:0 6px;height:4px;background:#ddd;border-radius:2px;position:relative}
.track::before{content:"";position:absolute;left:0;top:0;width:28px;height:4px;background:var(--red);border-radius:2px}
.time{font-size:11px;color:#888;margin-right:8px}
.city-tall{left:454px;top:0;width:432px;height:422px;background:linear-gradient(180deg,#bdbdbd,#7c7c7c 60%,#4d4d4d)}
.city-night{left:0;top:256px;width:534px;height:166px;background:linear-gradient(180deg,#1c1c1c,#6a6a6a 55%,#2a2a2a)}
.quote-line1{left:454px;top:218px;width:412px;height:36px;background:var(--red);color:var(--white);font-size:18px;text-align:right;padding:10px 7px 0 0;white-space:nowrap}
.quote-line2{left:534px;top:254px;width:332px;height:38px;background:var(--red);color:var(--white);font-family:"Bebas Neue",sans-serif;font-size:31px;text-align:right;padding:3px 6px 0 0;line-height:34px;white-space:nowrap}
.quote-by{left:742px;top:292px;width:136px;height:38px;background:var(--white);color:#444;font-style:italic;font-size:19px;text-align:right;padding:8px 8px 0 0;line-height:22px;white-space:nowrap}
.welcome{position:absolute;top:627px;left:0;width:1108px;text-align:center;font-size:25px;font-weight:400;color:#555}
.card{position:absolute;top:697px;width:286px;height:185px}
.card-diag{left:111px;background:radial-gradient(circle at 40% 40%,#ee1111,var(--red-dark));color:var(--white);text-align:center;padding-top:58px}
.card-diag h2{font-size:17px;font-weight:400;margin-bottom:10px}
.card-diag p{font-size:12px;font-style:italic;color:#222;line-height:15px;padding:0 38px}
.card-photo{background:linear-gradient(180deg,#d8d8d8,#9a9a9a)}
.card-photo .label{position:absolute;left:0;bottom:0;width:100%;height:46px;background:var(--red);color:var(--white);font-size:17px;text-align:center;line-height:46px}
.card-coach{left:412px}
.card-mgmt{left:710px}
.intro{position:absolute;left:0;width:1108px;text-align:center;font-size:12px;line-height:15.5px;color:#444}
.social{position:absolute;left:498px;top:1049px;display:flex;gap:13px}
.social span{width:27px;height:27px;background:#222}
.footer{position:absolute;top:1113px;left:0;width:1108px;text-align:center;font-size:11px;color:#666}
.footer .strong{color:#222}
.base-line{position:absolute;left:0;bottom:0;width:1108px;height:6px;background:var(--red)}
.base-notch{position:absolute;left:535px;bottom:6px;width:0;height:0;border-left:11px solid transparent;border-right:11px solid transparent;border-bottom:10px solid var(--red)}
</style>
</head>
<body>
<div class="top-bar"></div>
<div class="util-tab search">
  <svg width="14" height="14" viewBox="0 0 14 14"><circle cx="6" cy="6" r="4.2" fill="none" stroke="#fff" stroke-width="2"/><line x1="9" y1="9" x2="13" y2="13" stroke="#fff" stroke-width="2.4"/></svg>
</div>
<div class="util-tab account"><span>Sign in</span><span class="muted">|</span><span class="muted">Français</span></div>

<div class="logo"><span class="logo-mark"></span><span class="logo-name">tessel</span></div>

<nav class="main-nav">
  <a class="active" href="#">Home</a>
  <a href="#">Who we are</a>
  <a href="#">Cross the Tessel</a>
  <a href="#">Performance solutions</a>
  <a href="#">Sustain solutions</a>
  <a href="#">Join us</a>
</nav>

<div class="dashed" style="left:111px;top:139px;width:886px"></div>

<section class="hero">
  <div class="city-tall" role="img" aria-label="Black and white photo of glass office towers against a sky with contrails"></div>
  <div class="city-night" role="img" aria-label="Black and white photo of a city skyline at night across the water"></div>
  <div class="video">
    <div class="video-still" role="img" aria-label="Intro video still of a business team meeting"></div>
    <svg class="play" viewBox="0 0 56 56"><circle cx="28" cy="28" r="25" fill="none" stroke="#888" stroke-width="4"/><path d="M22 16 L38 28 L22 40Z" fill="#888"/></svg>
    <div class="play-label">CLICK TO PLAY</div>
    <div class="controls">
      <div class="btn"><svg width="10" height="12"><path d="M1 1 L9 6 L1 11Z" fill="#ccc"/></svg></div>
      <div class="track"></div>
      <span class="time">00.00</span>
      <div class="btn" style="width:30px"><svg width="14" height="12"><rect x="0" y="7" width="2" height="5" fill="#e3000f"/><rect x="4" y="5" width="2" height="7" fill="#e3000f"/><rect x="8" y="3" width="2" height="9" fill="#e3000f"/><rect x="12" y="1" width="2" height="11" fill="#ddd"/></svg></div>
      <div class="btn" style="width:30px;margin-left:1px"><svg width="18" height="12"><rect x="1" y="1" width="16" height="10" fill="none" stroke="#ccc" stroke-width="1.5"/><rect x="9" y="5" width="6" height="4" fill="#ccc"/></svg></div>
    </div>
  </div>
  <div class="quote-line1">Customer satisfaction is worthless,</div>
  <div class="quote-by">-Dana Whitlow</div>
  <div class="quote-line2">Customer loyalty is priceless.</div>
</section>

<h1 class="welcome">WELCOME TO TESSEL PERFORMANCE GROUP</h1>

<div class="card card-diag">
  <h2>BUSINESS DIAGNOSTICS</h2>
  <p>Lorem ipsum dolor sit amet, consectetur adipiscing elit. Nunc eget nisi et nibh</p>
</div>
<div class="card card-photo card-coach" role="img" aria-label="Photo of a smiling executive in front of an audience">
  <div class="label">EXECUTIVE COACHING</div>
</div>
<div class="card card-photo card-mgmt" role="img" aria-label="Photo of a business audience applauding">
  <div class="label">MANAGEMENT DEVELOPMENT</div>
</div>

<p class="intro" style="top:922px">Tessel Performance Group Inc. is the leading provider of profit generating and people development solutions. With the hands-on experience of best<br>practices, the state-of-the-art technology and in-depth information we help companies increase their efficiencies and profits. Frank, honest, committed,<br>valuable and rewarding are words that customers use to describe the quality services provided by Tessel Performance Group.</p>
<p class="intro" style="top:982px">Learn more about us, or find the right solutions for your specific business.We will be delighted to<br>help you achieve better business results.</p>

<div class="dashed" style="left:111px;top:1062px;width:377px"></div>
<div class="social" aria-label="Social links"><span></span><span></span><span></span></div>
<div class="dashed" style="left:612px;top:1062px;width:385px"></div>

<p class="footer">© Copyright 2013. All rights reserved. &nbsp;| &nbsp;Tessel Performance Group &nbsp;| &nbsp;88 Harbour Lane, Eastfield, NB E2A 1B1, Canada &nbsp;T :+1.800.555.0142 &nbsp;Email:info@tessel-momentum.example | <span class="strong">Site Map</span></p>

<div class="base-notch"></div>
<div class="base-line"></div>
</body>
</html>
```